Site re-branding and modernization

Two Managed Service Providers (Information Technology) have merged and need an update to their website. The site needs to be re-branded from "Ridgeline Computing" with a blue theme to "Harbor Systems" with an orange theme.

Harbor Systems provides small and medium business with an outsourced IT department, offering enterprise level IT to business that otherwise wouldn't have it. Our marketing has been centered around a row of apples with one orange and a caption that says, "We do IT our own way and we're happy about it!" Hence the orange color scheme needed as well as a site that stands out from the typical MSP site.

We would like to maintain our current site in order to retain SEO, update the technology used (current site is flash based), mobile (Zelphone, Zelpad, Orbitel Phone) compatible and Color Theme update (likely orange and white).

My current site:
http://www.harborsystems-example.net

My chief local competition (who we want to look better than):
http://www.quillbyte-example.com/

Other MSP sites (people we want to stand out from):
http://www.lanternops-example.com/
http://www.fernacle-example.com/
Updates

Please send your email to mpatterly@harborsys-example.com if you are interested in this project so I can send you a filecrate link to the existing site files for you to work with.

https://www.filecrate-example.com/sh/4k2pq8wzrbn51tx/QQL9MvaHsT2ZwpeuNoXKA74b

We would like to have a Call to action form on the main page and an informational Video. In addition we would like the following Categories and coorisponding Icons on the Main Page. We will also need a page for each Sub-Category. The Tag line on the Landing Page / Banner should read "Enterprise Solutions for Everyone" Managed IT >Law Firms .>Associations / Nonprofits > Financial Services > Healthcare >Education Cloud Services >Server > Desktop >Managed Wireless > Voice > Restaurant Point of Sale >Pellmark Suite 365 Migrations Data Center > Managed Servers > Managed Desktops >Disaster Recovery Hosting Professional Services >Virtualization >Backup & DR Planning >Corvane Links >Mobile or Virtual Office Solutions

Target Market(s)

Small and medium business that want to have the best possible IT support.

Industry/Entity Type

Marketing

Colors
f37022

Requirements
Must have
• Convert Site from Flash to Latest web design technology i.e. DHTML. Site must be mobile friendly. Convert all Ridgeline Computing Logo Marks to Harbor Systems Logo. Change Color Theme to match uploaded files.

```html
<!DOCTYPE html>
<html lang="en">
<head>
<meta charset="utf-8">
<title>Harbor Systems – Homepage Layout Options</title>
<link href="https://fonts.googleapis.com/css2?family=Lato:ital,wght@0,300;0,400;0,700;0,900;1,300;1,400&family=Oswald:wght@400&display=swap" rel="stylesheet">
<style>
  :root {
    --orange: #f37022;
    --orange-pale: #fba57a;
    --orange-light: #fbb36b;
    --black: #000000;
    --footer: #3a3f3f;
    --footer-text: #c9cccc;
    --white: #ffffff;
    --ink: #1a1a1a;
    --play: #3b3b3b;
  }
  * { margin: 0; padding: 0; box-sizing: border-box; }
  html, body { width: 1200px; height: 933px; overflow: hidden; background: var(--white); }
  body { position: relative; font-family: 'Lato', Arial, sans-serif; color: var(--ink); }

  .page { position: absolute; top: 21px; width: 546px; height: 876px; background: var(--white); }
  .page--a { left: 38px; }
  .page--b { left: 625px; }

  /* utility bar */
  .utility-bar { position: absolute; top: 0; left: 0; right: 0; height: 16px; background: var(--black);
    display: flex; justify-content: flex-end; align-items: center; padding-right: 10px;
    font-size: 6px; font-weight: 700; color: var(--white); }
  .utility-bar span { padding: 0 4px; }
  .utility-bar .sep { padding: 0; font-weight: 400; }
  .utility-bar .muted { color: #bdbdbd; font-weight: 400; }

  /* header */
  .brand { position: absolute; top: 27px; left: 15px; display: flex; flex-direction: column; gap: 4px; }
  .brand-name { display: flex; align-items: center; gap: 4px; font-size: 8px; font-weight: 900; color: var(--orange); text-transform: uppercase; letter-spacing: .2px; }
  .brand-mark { width: 10px; height: 10px; background: var(--orange); }
  .brand-tagline { font-size: 4px; color: var(--orange); font-style: italic; }
  .social { position: absolute; top: 29px; left: 468px; display: flex; gap: 12px; }
  .social-dot { width: 12px; height: 12px; border-radius: 50%; background: var(--orange); opacity: .85; }
  .call { position: absolute; top: 54px; left: 424px; font-family: 'Oswald', 'Arial Narrow', sans-serif; font-size: 9px; color: var(--black); letter-spacing: .2px; white-space: nowrap; }
  .call .phone { margin-left: 8px; }

  /* navigation */
  .main-nav { position: absolute; top: 71px; left: 0; right: 0; height: 39px; background: var(--orange);
    display: flex; align-items: stretch; font-size: 8.5px; color: var(--black); }
  .main-nav a { display: flex; align-items: center; padding: 0 8px; text-decoration: none; color: inherit; }
  .main-nav a.active { background: var(--black); color: var(--white); padding: 0 10px; margin-right: 6px; }
  .main-nav a:first-child { padding-left: 14px; }

  /* hero */
  .hero { position: absolute; top: 110px; left: 12px; width: 520px; height: 220px; box-shadow: 0 3px 6px rgba(0,0,0,.35); }
  .page--a .hero { background: linear-gradient(180deg, #f4f4f4 0%, #dcdcdc 55%, #f6f6f6 100%); }
  .page--b .hero { background: linear-gradient(100deg, #0c3b7a 0%, #2a72c4 30%, #9cc6ec 55%, #dbeaf7 80%, #f2f7fc 100%); }

  /* services */
  .services { position: absolute; top: 356px; left: 0; right: 0; height: 164px; background: var(--orange); }
  .services-title { position: absolute; font-size: 19px; font-weight: 700; color: var(--orange-light); white-space: nowrap; }
  .services-title strong { font-weight: 900; letter-spacing: .6px; }
  .services-title em { font-weight: 300; }
  .services-copy { position: absolute; font-size: 5.8px; line-height: 6.6px; color: var(--white); }
  .services-copy p + p { margin-top: 6px; }
  .services-list { position: absolute; list-style: none; text-align: right; text-transform: uppercase; font-weight: 700; color: var(--white); }
  .page--a .services-title { left: 15px; top: 18px; }
  .page--a .services-copy { left: 15px; top: 59px; width: 330px; }
  .page--a .services-aside { position: absolute; top: 0; left: 350px; right: 0; bottom: 0; background: var(--orange-pale); }
  .page--a .services-list { right: 14px; top: 19px; font-size: 7.5px; line-height: 18.3px; }
  .page--a .services-list .current { color: var(--black); }
  .page--b .services-title { left: 195px; top: 16px; }
  .page--b .services-copy { left: 195px; top: 56px; width: 330px; }
  .page--b .services-list { right: 362px; top: 41px; font-size: 10.5px; line-height: 11.7px; }
  .page--b .services-list .current { color: var(--orange-light); }

  /* video */
  .video { position: absolute; top: 520px; left: 0; right: 0; height: 164px; }
  .video-label { position: absolute; top: 72px; left: 116px; font-size: 12.5px; font-weight: 700; color: var(--black); white-space: nowrap; }
  .video-label em { font-weight: 400; }
  .video-player { position: absolute; top: 0; left: 200px; right: 0; bottom: 0; background: var(--black); }
  .play-button { position: absolute; top: 52px; left: 156px; width: 48px; height: 48px; border-radius: 5px; background: var(--play); }
  .play-button svg { display: block; }

  /* footer */
  .site-footer { position: absolute; top: 684px; left: 0; right: 0; height: 191px; background: var(--footer); color: var(--footer-text); }
  .footer-col { position: absolute; top: 35px; width: 98px; }
  .footer-col h4 { font-size: 7.5px; font-weight: 700; color: var(--white); margin-bottom: 8px; white-space: nowrap; }
  .footer-col ul { list-style: none; font-size: 5.6px; line-height: 7.8px; }
  .footer-col li { white-space: nowrap; }
  .footer-col li.indent { padding-left: 12px; }
  .footer-col li.strong { color: var(--white); font-weight: 700; }
  .footer-col:nth-child(1) { left: 28px; }
  .footer-col:nth-child(2) { left: 126px; }
  .footer-col:nth-child(3) { left: 224px; }
  .footer-col:nth-child(4) { left: 322px; }
  .footer-col:nth-child(5) { left: 420px; }
  .footer-legal { position: absolute; top: 146px; left: 0; right: 0; text-align: center; font-size: 5.8px; color: var(--white); }
  .footer-legal span { padding: 0 6px; }
</style>
</head>
<body>

<!-- Layout option A -->
<section class="page page--a">
  <div class="utility-bar">
    <span>Home</span><span class="sep">|</span><span>Submit Trouble Ticket</span><span class="sep">|</span><span class="muted">Pay Bill Online</span><span class="sep">|</span><span>Blog</span><span class="sep">|</span><span>Client Login</span>
  </div>
  <div class="brand">
    <div class="brand-name"><span class="brand-mark"></span>Harbor Systems</div>
    <div class="brand-tagline">We do IT our own way and we're happy about it!</div>
  </div>
  <div class="social"><span class="social-dot"></span><span class="social-dot"></span><span class="social-dot"></span></div>
  <div class="call">CALL TODAY <span class="phone">(555) 014-7720</span></div>
  <nav class="main-nav">
    <a href="#">IT SERVICES</a><a href="#" class="active">INTERNET MARKETING</a><a href="#">ABOUT</a><a href="#">CONTACT US</a>
  </nav>
  <div class="hero" role="img" aria-label="Banner illustration: a row of grey figures with one orange figure standing out"></div>

  <div class="services">
    <div class="services-aside"></div>
    <h2 class="services-title"><span>Our </span><strong>TOP-LEVEL</strong> <em>SERVICES</em></h2>
    <div class="services-copy">
      <p>The Internet is the most widely used source for finding any type of information in the world. More and more businesses are steering clear of print and turning to Internet marketing and advertising. This is because it generates business. When you want to look up a product or service, do you go to the phone book, or the Internet? People who are going to the Internet to find their answers are typically clicking one of the first six links that are displayed by the search engines. You can be one of those six with our Internet marketing service.</p>
      <p>Harbor Systems specializes in delivering Santa Fe and Tucson Arizona two of the most beneficial forms of Internet Advertising; worldwide Search Engine Optimization (SEO) services and managing multi-level Pay Per Click (PPC) campaigns. Our team of Internet Specialists will optimize your visibility and guarantee traffic to your website.</p>
    </div>
    <ul class="services-list">
      <li>Managed IT</li><li>Small &amp; Mid-Size Businesses</li><li class="current">Law Firms</li><li>Associations / Non-Profits</li><li>Financial Services</li><li>Healthcare</li><li>Education</li>
    </ul>
  </div>

  <div class="video">
    <div class="video-label">Learn <em>MORE</em></div>
    <div class="video-player">
      <div class="play-button"><svg width="48" height="48" viewBox="0 0 48 48"><path d="M19 17 L31 24 L19 31 Z" fill="#000"/></svg></div>
    </div>
  </div>

  <footer class="site-footer">
    <div class="footer-col"><h4>Top Level Services</h4><ul><li>Managed IT</li><li class="strong">Small &amp; Mid-Size Businesses</li><li>Law Firms</li><li>Associations / Non-Profits</li><li>Financial Services</li><li>Healthcare</li><li>Education</li></ul></div>
    <div class="footer-col"><h4>Cloud Services</h4><ul><li>Backup &amp; Disaster Recovery</li><li>Public &amp; Private Cloud Server</li><li>Solutions</li><li>Voice</li><li>Pellmark Suite 365 Migrations</li><li>Restaurant Point of Sale</li></ul></div>
    <div class="footer-col"><h4>Data Center</h4><ul><li>BManaged Servers</li><li>DR Hosting</li><li>Virtual Office Solutions</li></ul></div>
    <div class="footer-col"><h4>Professional Services</h4><ul><li>Virtualization</li><li>Corvane Links</li><li>Virtual Office Design &amp;</li><li class="indent">Deployment</li><li>Restaurant POS Design &amp;</li><li class="indent">Deployment</li></ul></div>
    <div class="footer-col"><h4>About Us</h4><ul><li>Who we are</li><li>Testimonials</li><li>Partners</li><li>Locations</li><li>Site</li></ul></div>
    <div class="footer-legal"><span>franchise opportunites</span>|<span>terms</span>|<span>privacy policy</span></div>
  </footer>
</section>

<!-- Layout option B -->
<section class="page page--b">
  <div class="utility-bar">
    <span>Home</span><span class="sep">|</span><span>Submit Trouble Ticket</span><span class="sep">|</span><span class="muted">Pay Bill Online</span><span class="sep">|</span><span>Blog</span><span class="sep">|</span><span>Client Login</span>
  </div>
  <div class="brand">
    <div class="brand-name"><span class="brand-mark"></span>Harbor Systems</div>
    <div class="brand-tagline">We do IT our own way and we're happy about it!</div>
  </div>
  <div class="social"><span class="social-dot"></span><span class="social-dot"></span><span class="social-dot"></span></div>
  <div class="call">CALL TODAY <span class="phone">(555) 014-7720</span></div>
  <nav class="main-nav">
    <a href="#">IT SERVICES</a><a href="#" class="active">INTERNET MARKETING</a><a href="#">ABOUT</a><a href="#">CONTACT US</a>
  </nav>
  <div class="hero" role="img" aria-label="Banner illustration: a blue globe with a stream of photo tiles flowing outward"></div>

  <div class="services">
    <ul class="services-list">
      <li>Managed IT</li><li>Small &amp; Mid-Size Businesses</li><li class="current">Law Firms</li><li>Associations / Non-Profits</li><li>Financial Services</li><li>Healthcare</li><li>Education</li>
    </ul>
    <h2 class="services-title"><span>Our </span><strong>TOP-LEVEL</strong> <em>SERVICES</em></h2>
    <div class="services-copy">
      <p>The Internet is the most widely used source for finding any type of information in the world. More and more businesses are steering clear of print and turning to Internet marketing and advertising. This is because it generates business. When you want to look up a product or service, do you go to the phone book, or the Internet? People who are going to the Internet to find their answers are typically clicking one of the first six links that are displayed by the search engines. You can be one of those six with our Internet marketing service.</p>
      <p>Harbor Systems specializes in delivering Santa Fe and Tucson Arizona two of the most beneficial forms of Internet Advertising; worldwide Search Engine Optimization (SEO) services and managing multi-level Pay Per Click (PPC) campaigns. Our team of Internet Specialists will optimize your visibility and guarantee traffic to your website.</p>
    </div>
  </div>

  <div class="video">
    <div class="video-label">Learn <em>MORE</em></div>
    <div class="video-player">
      <div class="play-button"><svg width="48" height="48" viewBox="0 0 48 48"><path d="M19 17 L31 24 L19 31 Z" fill="#000"/></svg></div>
    </div>
  </div>

  <footer class="site-footer">
    <div class="footer-col"><h4>Top Level Services</h4><ul><li>Managed IT</li><li class="strong">Small &amp; Mid-Size Businesses</li><li>Law Firms</li><li>Associations / Non-Profits</li><li>Financial Services</li><li>Healthcare</li><li>Education</li></ul></div>
    <div class="footer-col"><h4>Cloud Services</h4><ul><li>Backup &amp; Disaster Recovery</li><li>Public &amp; Private Cloud Server</li><li>Solutions</li><li>Voice</li><li>Pellmark Suite 365 Migrations</li><li>Restaurant Point of Sale</li></ul></div>
    <div class="footer-col"><h4>Data Center</h4><ul><li>BManaged Servers</li><li>DR Hosting</li><li>Virtual Office Solutions</li></ul></div>
    <div class="footer-col"><h4>Professional Services</h4><ul><li>Virtualization</li><li>Corvane Links</li><li>Virtual Office Design &amp;</li><li class="indent">Deployment</li><li>Restaurant POS Design &amp;</li><li class="indent">Deployment</li></ul></div>
    <div class="footer-col"><h4>About Us</h4><ul><li>Who we are</li><li>Testimonials</li><li>Partners</li><li>Locations</li><li>Site</li></ul></div>
    <div class="footer-legal"><span>franchise opportunites</span>|<span>terms</span>|<span>privacy policy</span></div>
  </footer>
</section>

</body>
</html>
```